Professional & attention grabbing.

A business card design, front and back. I already have a logo I will attach, but I am open to something new as well.
Things to include:
Name:
Title:
Phone:
Email:
Wanting something that is professional but attention grabbing.
Also we do a lot of work using drones on natural gas pipelines (leading the future)if you want to include any of that. I'm open to ideas.
Target Market(s)
Natural gas transmission industry / greenhouse gas mitigation industry
Industry/Entity Type
Business
Colors
Designer to choose colors to be used in the design.
Look and feel
Each slider illustrates characteristics of the customer's brand and the style your logo design should communicate.

```html
<!DOCTYPE html>
<html lang="en">
<head>
<meta charset="utf-8">
<title>Kestrel Field Inspections – Business Card</title>
<link href="https://fonts.googleapis.com/css2?family=Montserrat:wght@400;500;700&display=swap" rel="stylesheet">
<style>
  :root {
    --backdrop: #2b2b2d;
    --card: #ffffff;
    --ink: #3a3a3c;
    --accent: #c01f26;
    --card-radius: 34px;
  }
  * { box-sizing: border-box; margin: 0; padding: 0; }
  html, body {
    width: 1200px;
    height: 1000px;
    overflow: hidden;
    background: var(--backdrop);
    font-family: "Montserrat", Arial, sans-serif;
  }
  .stage {
    width: 1200px;
    height: 1000px;
    display: flex;
    flex-direction: column;
    align-items: center;
    justify-content: center;
    gap: 50px;
  }
  .card {
    position: relative;
    width: 760px;
    height: 420px;
    background: var(--card);
    border-radius: var(--card-radius);
    box-shadow: 0 14px 30px rgba(0,0,0,0.45);
  }
  .brand {
    display: flex;
    align-items: center;
    gap: 18px;
    color: var(--ink);
    font-weight: 700;
    text-transform: uppercase;
    letter-spacing: 0.5px;
    line-height: 1;
  }
  .brand-mark {
    width: 34px;
    height: 34px;
    background: var(--accent);
    flex: none;
  }
  .card-front .brand {
    position: absolute;
    left: 50%;
    top: 50%;
    transform: translate(-50%, -50%);
    font-size: 30px;
    white-space: nowrap;
  }
  .card-back .brand {
    position: absolute;
    right: 60px;
    top: 150px;
    font-size: 22px;
    gap: 14px;
    white-space: nowrap;
  }
  .card-back .brand-mark { width: 26px; height: 26px; }
  .holder {
    position: absolute;
    left: 60px;
    top: 130px;
  }
  .holder-name {
    color: var(--accent);
    font-weight: 700;
    font-size: 26px;
    letter-spacing: 0.5px;
    text-transform: uppercase;
  }
  .holder-title {
    color: var(--ink);
    font-weight: 500;
    font-size: 16px;
    letter-spacing: 1px;
    text-transform: uppercase;
    margin-top: 4px;
  }
  .contact {
    position: absolute;
    left: 60px;
    bottom: 50px;
    list-style: none;
    color: var(--ink);
    font-size: 15px;
    line-height: 1.6;
  }
  .contact-label {
    color: var(--accent);
    font-weight: 700;
    margin-right: 4px;
  }
</style>
</head>
<body>
  <main class="stage">
    <section class="card card-front" aria-label="Card front">
      <div class="brand">
        <span class="brand-mark"></span>
        <span class="brand-name">Kestrel Field Inspections</span>
      </div>
    </section>

    <section class="card card-back" aria-label="Card back">
      <div class="holder">
        <p class="holder-name">Daniel Harper</p>
        <p class="holder-title">Founder</p>
      </div>
      <div class="brand">
        <span class="brand-mark"></span>
        <span class="brand-name">Kestrel Field Inspections</span>
      </div>
      <ul class="contact">
        <li><span class="contact-label">P:</span>000 000 0000</li>
        <li><span class="contact-label">E:</span>info@yourmail.com</li>
      </ul>
    </section>
  </main>
</body>
</html>
```